Harbor Ridge Painting Epoxy Flyer

We need a promotional flyer for a new epoxy floor coatings division of our painting company. We do epoxy garage floor coatings and paver sealing. It needs to be based on and very similar to the attached flyer. The garage floor picture needs to look more realistic, and the before and after pavers pictures should look less shiny but still a good contrast. Include attached logo

```html
<!DOCTYPE html>
<html lang="en">
<head>
<meta charset="utf-8">
<title>Harbor Ridge Painting – Epoxy &amp; Paver Sealing Flyer</title>
<link rel="stylesheet" href="https://fonts.googleapis.com/css2?family=Oswald:wght@500;600;700&family=Poppins:wght@400;500;600;700&display=swap">
<style>
  :root{
    --green:#4ea823;
    --green-dark:#35761f;
    --blue:#2a8ddc;
    --orange:#c7700a;
    --ink:#0d0d0d;
    --bg-top:#e8f2fb;
    --bg-mid:#edf5ec;
    --bg-bottom:#f6f1e6;
    --white:#ffffff;
  }
  *{margin:0;padding:0;box-sizing:border-box}
  html,body{width:904px;height:1200px;overflow:hidden}
  body{font-family:"Poppins",sans-serif;color:var(--ink)}
  .flyer{position:relative;width:904px;height:1200px;overflow:hidden;
    background:linear-gradient(180deg,var(--bg-top) 0%,var(--bg-mid) 45%,var(--bg-bottom) 88%)}
  .hero{position:absolute;left:0;top:0}

  .brand{position:absolute;left:598px;top:112px;display:flex;align-items:center;gap:10px}
  .brand-dot{width:18px;height:18px;border-radius:50%;background:var(--green)}
  .brand-name{font-family:"Poppins",sans-serif;font-weight:600;font-size:17px;line-height:1;color:var(--ink);letter-spacing:.3px;text-transform:uppercase;white-space:nowrap}

  .kicker{position:absolute;top:499px;left:0;width:904px;display:flex;justify-content:center;align-items:center;gap:14px}
  .kicker-rule{width:190px;height:3px;background:linear-gradient(90deg,#b9d8d0,#c9e0b8)}
  .kicker-word{font-family:"Oswald",sans-serif;font-weight:700;font-size:56px;line-height:1;
    background:linear-gradient(180deg,var(--blue) 0%,var(--green) 45%,var(--orange) 100%);
    -webkit-background-clip:text;background-clip:text;color:transparent}
  .headline{position:absolute;top:553px;left:0;width:904px;text-align:center;font-family:"Oswald",sans-serif;font-weight:700;font-size:61px;line-height:1;letter-spacing:-.3px;white-space:nowrap}
  .subline{position:absolute;top:614px;left:0;width:904px;text-align:center;font-family:"Poppins",sans-serif;font-weight:400;font-size:53px;line-height:1;white-space:nowrap}

  .service{position:absolute;top:697px;width:388px;height:202px;border:2px solid var(--orange);border-top-color:var(--blue);border-radius:14px}
  .service.epoxy{left:46px}
  .service.pavers{left:470px}
  .service-title{position:absolute;top:-22px;left:24px;right:24px;height:41px;border-radius:21px;color:var(--white);
    font-family:"Oswald",sans-serif;font-weight:600;font-size:33px;line-height:41px;text-align:center;white-space:nowrap}
  .epoxy .service-title{background:var(--blue)}
  .pavers .service-title{background:var(--green)}
  .service-list{list-style:none;position:absolute;top:45px;left:48px;right:6px}
  .pavers .service-list{left:24px}
  .service-list li{position:relative;padding-left:24px;font-weight:500;font-size:19.5px;line-height:20.6px;margin-bottom:13.4px;white-space:nowrap}
  .service-list li::before{content:"";position:absolute;left:0;top:3px;width:15px;height:15px;border-radius:50%}
  .epoxy .service-list li::before{background:var(--blue)}
  .pavers .service-list li::before{background:var(--green)}
  .service-list li::after{content:"";position:absolute;left:5px;top:5.5px;width:3.5px;height:7px;border:solid var(--white);border-width:0 2px 2px 0;transform:rotate(40deg)}

  .tagline{position:absolute;top:927px;left:0;width:904px;text-align:center;font-family:"Oswald",sans-serif;font-weight:600;font-size:36.5px;line-height:1.2;white-space:nowrap}

  .trust{position:absolute;top:990px;display:flex;align-items:center;gap:21px}
  .trust-icon{width:60px;height:60px;flex:none;border-radius:50%;border:1.5px solid #c9a36a;background:var(--white);display:flex;align-items:center;justify-content:center}
  .trust-text{font-family:"Oswald",sans-serif;font-weight:500;font-size:25px;line-height:1.05;white-space:nowrap}
  .trust.licensed{left:70px}
  .trust.family{left:308px}
  .trust.area{left:575px}

  .cta{position:absolute;left:0;top:1078px;width:904px;height:122px;background:var(--green-dark);color:var(--white)}
  .cta-ask{position:absolute;left:65px;top:16px;font-family:"Oswald",sans-serif;font-weight:700;line-height:1}
  .cta-ask .small{display:block;font-size:33px;letter-spacing:.5px}
  .cta-ask .big{display:block;font-size:56px;letter-spacing:3px;margin-top:-1px}
  .cta-phone-icon{position:absolute;left:340px;top:22px;width:46px;height:46px;border-radius:50%;
    background:linear-gradient(135deg,var(--blue),var(--green),var(--orange));display:flex;align-items:center;justify-content:center}
  .cta-phone{position:absolute;left:401px;top:25px;font-family:"Poppins",sans-serif;font-weight:600;font-size:50px;line-height:1;letter-spacing:6px;white-space:nowrap}
  .cta-note{position:absolute;left:340px;top:75px;font-family:"Poppins",sans-serif;font-weight:500;font-size:23px;line-height:1;letter-spacing:.4px;white-space:nowrap}
</style>
</head>
<body>
<main class="flyer">

  <svg class="hero" width="904" height="500" viewBox="0 0 904 500">
    <defs>
      <linearGradient id="cornerFill" x1="0" y1="0" x2="0" y2="310" gradientUnits="userSpaceOnUse">
        <stop offset="0" stop-color="#4ea823"/>
        <stop offset=".72" stop-color="#5c9f1f"/>
        <stop offset="1" stop-color="#c7700a"/>
      </linearGradient>
      <linearGradient id="outerArc" x1="20" y1="0" x2="550" y2="0" gradientUnits="userSpaceOnUse">
        <stop offset="0" stop-color="#3aa66a"/>
        <stop offset=".15" stop-color="#2a8ddc"/>
        <stop offset=".75" stop-color="#2a8ddc"/>
        <stop offset="1" stop-color="#3aa66a"/>
      </linearGradient>
      <linearGradient id="innerArc" x1="0" y1="20" x2="0" y2="480" gradientUnits="userSpaceOnUse">
        <stop offset="0" stop-color="#4ea823"/>
        <stop offset=".5" stop-color="#4ea823"/>
        <stop offset=".85" stop-color="#c7700a"/>
        <stop offset="1" stop-color="#c7700a"/>
      </linearGradient>
      <linearGradient id="paverBefore" x1="0" y1="0" x2="0" y2="1">
        <stop offset="0" stop-color="#7d7c78"/>
        <stop offset="1" stop-color="#6a645c"/>
      </linearGradient>
      <linearGradient id="paverAfter" x1="0" y1="0" x2="0" y2="1">
        <stop offset="0" stop-color="#a8abaf"/>
        <stop offset="1" stop-color="#93979c"/>
      </linearGradient>
      <linearGradient id="garageBefore" x1="0" y1="0" x2="0" y2="1">
        <stop offset="0" stop-color="#c8c6c2"/>
        <stop offset="1" stop-color="#e2e3e5"/>
      </linearGradient>
      <linearGradient id="garageAfter" x1="0" y1="0" x2="0" y2="1">
        <stop offset="0" stop-color="#bdbcbb"/>
        <stop offset="1" stop-color="#9c9b9a"/>
      </linearGradient>
      <clipPath id="bigPhoto"><circle cx="294" cy="245" r="210"/></clipPath>
      <clipPath id="smallPhoto"><circle cx="527" cy="318" r="126"/></clipPath>
    </defs>

    <path d="M0 0 H410 C220 18 70 120 42 300 L0 306 Z" fill="url(#cornerFill)"/>

    <path d="M23 224 A272 240 0 0 1 548 159" fill="none" stroke="url(#outerArc)" stroke-width="11"/>
    <path d="M294 20 A262 230 0 1 0 378 447" fill="none" stroke="url(#innerArc)" stroke-width="12"/>

    <circle cx="294" cy="245" r="218" fill="#ffffff"/>
    <g clip-path="url(#bigPhoto)">
      <rect role="img" aria-label="Paver walkway before sealing, dull and weathered" x="84" y="35" width="210" height="420" fill="url(#paverBefore)"/>
      <rect role="img" aria-label="Paver walkway after sealing, clean with restored color" x="294" y="35" width="210" height="420" fill="url(#paverAfter)"/>
      <rect x="84" y="35" width="420" height="81" fill="#4ea823"/>
      <rect x="292" y="35" width="3" height="420" fill="#ffffff"/>
    </g>
    <text x="238" y="100" text-anchor="middle" font-family="Oswald, sans-serif" font-weight="700" font-size="27" fill="#ffffff">Before</text>
    <text x="352" y="100" text-anchor="middle" font-family="Oswald, sans-serif" font-weight="700" font-size="27" fill="#ffffff">After</text>

    <circle cx="527" cy="318" r="140" fill="#ffffff"/>
    <g clip-path="url(#smallPhoto)">
      <rect role="img" aria-label="Garage floor before epoxy coating, bare worn concrete" x="401" y="192" width="124" height="252" fill="url(#garageBefore)"/>
      <rect role="img" aria-label="Garage floor after epoxy coating, grey speckled finish" x="531" y="192" width="124" height="252" fill="url(#garageAfter)"/>
    </g>
    <rect x="434" y="301" width="87" height="17" fill="#4ea823"/>
    <rect x="531" y="301" width="88" height="17" fill="#4ea823"/>
    <text x="477" y="314" text-anchor="middle" font-family="Oswald, sans-serif" font-weight="600" font-size="12" fill="#ffffff">Before</text>
    <text x="575" y="314" text-anchor="middle" font-family="Oswald, sans-serif" font-weight="600" font-size="12" fill="#ffffff">After</text>
  </svg>

  <div class="brand">
    <span class="brand-dot"></span>
    <span class="brand-name">Harbor Ridge Painting</span>
  </div>

  <div class="kicker">
    <span class="kicker-rule"></span>
    <span class="kicker-word">EPOXY</span>
    <span class="kicker-rule"></span>
  </div>
  <h1 class="headline">Upgrade Your Garage &amp; Driveway</h1>
  <p class="subline">FROM WORN-OUT TO LIKE NEW</p>

  <section class="service epoxy">
    <h2 class="service-title">Epoxy Floor Coatings</h2>
    <ul class="service-list">
      <li>Durable, long-lasting finish</li>
      <li>Slip-resistant texture</li>
      <li>Covers cracks &amp;<br>imperfections</li>
      <li>Easy to clean &amp; maintain</li>
    </ul>
  </section>

  <section class="service pavers">
    <h2 class="service-title">Paver Sealing</h2>
    <ul class="service-list">
      <li>Restores color &amp; enhances<br>appearance</li>
      <li>Protects from sun fading</li>
      <li>Helps prevent weeds &amp; sand loss</li>
      <li>Easier to clean &amp; maintain</li>
    </ul>
  </section>

  <p class="tagline">Practical upgrades that protect and improve your home</p>

  <div class="trust licensed">
    <span class="trust-icon">
      <svg width="30" height="30" viewBox="0 0 26 26"><circle cx="13" cy="13" r="10" fill="none" stroke="#4ea823" stroke-width="2.5"/><path d="M8 13 l4 4 l7 -8" fill="none" stroke="#2a8ddc" stroke-width="2.8" stroke-linecap="round" stroke-linejoin="round"/></svg>
    </span>
    <span class="trust-text">Licensed &amp;<br>Insured</span>
  </div>
  <div class="trust family">
    <span class="trust-icon">
      <svg width="30" height="30" viewBox="0 0 26 26"><path d="M13 3 L22 6 V13 C22 18 18 22 13 24 C8 22 4 18 4 13 V6 Z" fill="#3aa66a"/><path d="M9 13 l3 3 l5 -6" fill="none" stroke="#ffffff" stroke-width="2.2" stroke-linecap="round" stroke-linejoin="round"/></svg>
    </span>
    <span class="trust-text">Family-Owned<br>Local Business</span>
  </div>
  <div class="trust area">
    <span class="trust-icon">
      <svg width="30" height="30" viewBox="0 0 26 26"><ellipse cx="13" cy="22" rx="8" ry="2.5" fill="none" stroke="#c7700a" stroke-width="1.6"/><path d="M13 21 C9 15 7 12 7 9 a6 6 0 0 1 12 0 c0 3 -2 6 -6 12 Z" fill="#2a8ddc"/><circle cx="13" cy="9" r="2.3" fill="#ffffff"/></svg>
    </span>
    <span class="trust-text">Serving Prescott &amp;<br>Surrounding Areas</span>
  </div>

  <footer class="cta">
    <p class="cta-ask"><span class="small">CALL FOR A FREE</span><span class="big">ESTIMATE</span></p>
    <span class="cta-phone-icon">
      <svg width="22" height="22" viewBox="0 0 24 24"><path d="M6.6 10.8c1.4 2.8 3.8 5.1 6.6 6.6l2.2-2.2c.3-.3.7-.4 1-.2 1.1.4 2.3.6 3.6.6.6 0 1 .4 1 1V20c0 .6-.4 1-1 1C10.6 21 3 13.4 3 4c0-.6.4-1 1-1h3.5c.6 0 1 .4 1 1 0 1.3.2 2.5.6 3.6.1.3 0 .7-.2 1z" fill="#ffffff"/></svg>
    </span>
    <p class="cta-phone">928-555-0147</p>
    <p class="cta-note">Fast, professional service you can trust</p>
  </footer>

</main>
</body>
</html>
```